Business Cards - Brightpath Horizon

need to design unique business card for my mortgage business. I need to design credit card style business card for my business or any unique idea that you might have

Target Market(s)

Home Loan customers

Industry/Entity Type

Mortgage Brokerage

Contact Information for Business Card

please design credit card style or very unique style business card

Colors

Designer to choose colors to be used in the design.

Requirements
Must have
• Name
• position
• Phone number
• fax number
• email address
• website address
• social media address
• All above fields will be provided once design in finalised

```html
<!DOCTYPE html>
<html lang="en">
<head>
<meta charset="utf-8">
<title>Brightpath Horizon – Business Card</title>
<link rel="stylesheet" href="https://fonts.googleapis.com/css2?family=Tinos:wght@400;700&family=Orbitron:wght@500&display=swap">
<style>
  :root {
    --page-bg: #e6e8ec;
    --card-bg: #ffffff;
    --navy: #1c2a8f;
    --orange: #f0931e;
    --text-grey: #4a4a4a;
    --decor-tint: #dde1ee;
    --icon-fill: #8a93b8;
  }
  * { margin: 0; padding: 0; box-sizing: border-box; }
  html, body {
    width: 1200px;
    height: 901px;
    overflow: hidden;
    background: var(--page-bg);
  }
  .card {
    position: absolute;
    left: 100px;
    top: 135px;
    width: 1000px;
    height: 630px;
    background: var(--card-bg);
    border-radius: 30px;
    overflow: hidden;
    box-shadow: 0 12px 40px rgba(20, 30, 60, 0.18);
    font-family: "Tinos", "Times New Roman", serif;
  }
  .card__backdrop {
    position: absolute;
    left: 0;
    top: 0;
    width: 680px;
    height: 520px;
    background: radial-gradient(ellipse at 30% 45%, var(--decor-tint) 0%, rgba(221, 225, 238, 0.45) 45%, rgba(255, 255, 255, 0) 75%);
  }
  .brand {
    position: absolute;
    right: 50px;
    top: 80px;
    text-align: center;
    color: var(--navy);
    font-weight: 400;
    line-height: 1;
  }
  .brand__line-top { display: block; font-size: 40px; letter-spacing: 3px; }
  .brand__line-main { display: block; font-size: 70px; letter-spacing: 1px; margin-top: 6px; }
  .holder {
    position: absolute;
    left: 59px;
    top: 368px;
  }
  .holder__name {
    color: var(--navy);
    font-size: 36px;
    font-weight: 400;
    letter-spacing: 0.5px;
  }
  .holder__role {
    color: var(--orange);
    font-size: 27px;
    margin-top: 6px;
  }
  .hotline {
    position: absolute;
    right: 45px;
    top: 372px;
    font-family: "Orbitron", "Courier New", monospace;
    font-weight: 500;
    font-size: 58px;
    letter-spacing: 4px;
    color: var(--navy);
  }
  .divider {
    position: absolute;
    left: 59px;
    top: 478px;
    width: 900px;
    height: 2px;
    background: linear-gradient(90deg, var(--orange) 0%, var(--orange) 70%, rgba(240, 147, 30, 0.2) 100%);
  }
  .contact {
    position: absolute;
    top: 505px;
    font-size: 25px;
    line-height: 36px;
    color: var(--text-grey);
  }
  .contact--direct { left: 59px; }
  .contact--address { left: 361px; }
  .contact__label { color: var(--navy); font-weight: 700; }
  .online {
    position: absolute;
    right: 55px;
    top: 505px;
    text-align: right;
  }
  .online__icons { height: 36px; }
  .online__site {
    font-size: 25px;
    font-weight: 700;
    color: var(--text-grey);
    line-height: 36px;
  }
</style>
</head>
<body>
  <div class="card">
    <div class="card__backdrop" role="img" aria-label="Faint house roof outline with window decoration"></div>

    <div class="brand">
      <span class="brand__line-top">BRIGHTPATH</span>
      <span class="brand__line-main">HORIZON</span>
    </div>

    <div class="holder">
      <div class="holder__name">DANIEL REEVE</div>
      <div class="holder__role">CEO/FOUNDER</div>
    </div>

    <div class="hotline">718 305 6621</div>

    <div class="divider"></div>

    <div class="contact contact--direct">
      <div><span class="contact__label">P:</span> 503 218 7746</div>
      <div>dan@bphorizon.com</div>
    </div>

    <div class="contact contact--address">
      <div>4120 Cedar Crest Road</div>
      <div>Boulder, Colorado 80302</div>
    </div>

    <div class="online">
      <svg class="online__icons" width="150" height="36" viewBox="0 0 150 36" aria-label="Social media links">
        <circle cx="18" cy="18" r="16" fill="var(--icon-fill)"/>
        <circle cx="56" cy="18" r="16" fill="var(--icon-fill)"/>
        <circle cx="94" cy="18" r="16" fill="var(--icon-fill)"/>
        <circle cx="132" cy="18" r="16" fill="var(--icon-fill)"/>
      </svg>
      <div class="online__site">www.bphorizon.com</div>
    </div>
  </div>
</body>
</html>
```